Home Page for a Swiss based start up company, trading Natural & Health food ingredients (B2B)

I would like to create a home page for my new start up company (Veltrana Swiss AG), the main field of activity is the trading and marketing of Natural and Health food ingredients towards the functional Food and Food supplements industry. (B2B).
Target Market : Functional Food and Food Supplement Manufacturers (B2B) based in Switzerland and Europe
The values I would like to convey are :
- sourcing of natural and health ingredients, (example : natural plant extracts, Omega 3, plant proteins, natural vitamins, vegan food ingredients...etc)
- Health & Nutritional Health
- Eco-friendly and Sustainability
- High Quality Standard in term of products and logistic services
- Trust and reliability
- Flexibility & speed to market
-Technical advice for the development of new products

The site will be translated in 3 languages (German, French, English)
Number of web pages : 5 : Home, About us, Products, Our Services, Contact

See here below attached Logo file.

Here some link of websites which can be taken as benchmark or source of inspiration
- https://quorbelix.com
- https://www.dralvimo.com/

Target Market(s)

Manufacturers of Functional Foods and Food Supplements in Switzerland and Europe (B2B)

Industry/Entity Type

B2B Trading of Natural & Health Ingredients

Coding

Number of Pages Required

Font styles to use
Sans Serif

Colors
0054AA
0677BA
7BADD7
CADEEF
E8F1F8
0094D4
00A9DD
6FCCEA
C7EBF8
E9F6FB
00AB8E
00BBA5
67D7C9
C6EFE9
E9F9F6
59FF00
82FF00
B8FF75
E3FFCB
F4FFEA
FFF300
FFF600
FEFA6F
FFFEC7
FFFEE8
FFC000
F8CF3A
FAE287
FDF2CF
FEFAEE
F0912C
F2A743
F7CA91
FBE8D2
FDF5EE
EE7325
F08F49
F5BC92
FAE3D3
FDF4ED

Requirements
Must have
• inspiration towards nature, sustainability, vegan food, functional food & beverages, food supplements, nutritional health, low carbon footprint
Should not have
• animals, chemistry, food additives

```html
<!DOCTYPE html>
<html lang="en">
<head>
<meta charset="utf-8">
<title>Veltrana Swiss AG – Natural &amp; Functional Ingredients Trader</title>
<link href="https://fonts.googleapis.com/css2?family=Josefin+Sans:wght@300;400;600;700&display=swap" rel="stylesheet">
<style>
:root{
  --green:#5b8a10;
  --green-dark:#3f6a08;
  --red:#d8261d;
  --pale-green:#eef4cc;
  --gray-bg:#f1f2f4;
  --ink:#1d1d1d;
  --muted:#6b6b6b;
  --footer:#1d211b;
  --white:#fff;
}
*{box-sizing:border-box;margin:0;padding:0}
html,body{width:1200px;height:4000px;overflow:hidden;background:var(--white)}
body{font-family:"Josefin Sans",sans-serif;color:var(--ink);position:relative}
.abs{position:absolute}
.center{text-align:center;left:0;width:1200px}
.btn{position:absolute;display:flex;align-items:center;justify-content:center;gap:14px;background:var(--red);color:#fff;font-weight:700;font-size:18px;border-radius:0 28px 28px 0}
.btn .arr{width:24px;height:24px;border-radius:50%;background:rgba(255,255,255,.3);display:flex;align-items:center;justify-content:center}
.eyebrow{position:absolute;color:var(--red);font-size:16px}
.h2{position:absolute;font-weight:700;font-size:44px;line-height:1}

/* top bar & header */
.topbar{top:0;left:0;width:1200px;height:22px;background:var(--green);color:#fff;font-size:12px;font-weight:600}
.topbar span{position:absolute;left:157px;top:5px}
.topbar .soc{position:absolute;top:6px;width:10px;height:10px;border-radius:2px;background:#fff;opacity:.9}
.header{top:22px;left:0;width:1200px;height:76px;border-bottom:1px solid #eee}
.logo{position:absolute;display:flex;align-items:center;gap:8px;color:var(--green);font-weight:700}
.logo i{width:30px;height:30px;border-radius:50%;background:var(--green);display:block}
.nav a{position:absolute;top:33px;font-size:13px;color:var(--ink);text-decoration:none}
.vline{position:absolute;width:1px;background:#e5e5e5}

/* hero */
.hero-photo{top:98px;left:0;width:1200px;height:522px;background:radial-gradient(circle at 15% 30%,#c9782a 0,transparent 22%),radial-gradient(circle at 85% 25%,#e8c45a 0,transparent 18%),linear-gradient(120deg,#5a3620,#7a4a2a 45%,#5b3a22)}
.hero-text{color:#fff}
.arrow-btn{position:absolute;width:38px;height:38px;border-radius:50%;background:#fff;display:flex;align-items:center;justify-content:center}

/* features */
.feat{position:absolute;top:678px;height:78px;width:280px;background:var(--pale-green);border-radius:39px 0 0 39px}
.feat svg{position:absolute;left:20px;top:18px}
.feat b{position:absolute;left:84px;top:22px;font-size:18px}
.feat small{position:absolute;left:84px;top:45px;font-size:12px;color:var(--muted)}

/* values */
.values-bg{top:820px;left:0;width:1200px;height:546px;background:var(--gray-bg)}
.pill{position:absolute;width:326px;height:68px;background:#fff;border-radius:34px;display:flex;align-items:center;gap:16px;padding-left:14px;font-size:14px;line-height:1.4}
.pill i{width:46px;height:46px;border-radius:50%;border:1px solid #e2e2e2;flex:none;display:flex;align-items:center;justify-content:center}
.pill i::after{content:"";width:26px;height:26px;border-radius:50%;background:var(--c)}
.bottle{top:1025px;left:512px;width:311px;height:341px;background:radial-gradient(ellipse at 50% 80%,#4b7a2a 0,#8fae62 40%,transparent 70%),radial-gradient(ellipse at 50% 45%,#5a3514 0,#5a3514 18%,transparent 20%)}

/* ingredients */
.ing-img{position:absolute;top:1529px;width:281px;height:209px}
.ing-label{position:absolute;top:1718px;width:202px;height:40px;border-radius:20px;background:var(--pale-green);font-size:16px;display:flex;align-items:center;justify-content:center}

/* offer */
.offer-bg{top:1926px;left:0;width:1200px;height:405px;background:linear-gradient(90deg,#e8ebee,#eef0f2)}
.offer-img{top:1926px;left:683px;width:517px;height:405px;background:radial-gradient(circle at 70% 60%,#f2a744 0,#f2a744 16%,transparent 30%),radial-gradient(circle at 30% 30%,#3f6a1f 0,transparent 45%),linear-gradient(135deg,#6c8f48,#b5884e 60%,#d9d2c4)}
.count{position:absolute;top:2124px;width:36px;height:36px;border-radius:50%;background:#fff;display:flex;align-items:center;justify-content:center;font-size:14px}
.count-l{position:absolute;top:2168px;font-size:10px;width:60px;text-align:center}

/* news */
.news-img{position:absolute;top:3016px;width:281px;height:208px}
.date{position:absolute;top:2992px;width:48px;height:48px;border-radius:50%;background:#fff;font-size:13px;font-weight:700;text-align:center;line-height:1;padding-top:9px}
.meta{position:absolute;top:3247px;font-size:13px;color:var(--muted)}
.ntitle{position:absolute;top:3284px;font-size:17px;font-weight:700;line-height:1.4;width:290px}
.dot{position:absolute;top:3362px;width:8px;height:8px;border-radius:50%;background:#bbb}

/* newsletter & footer */
.footer-bg{top:3555px;left:0;width:1200px;height:445px;background:var(--footer)}
.news-red{top:3433px;left:155px;width:357px;height:168px;background:var(--red);border-radius:12px 0 0 12px;color:#fff}
.news-green{top:3433px;left:512px;width:531px;height:168px;background:#eef5d2;border-radius:0 12px 12px 0}
.f-ico{position:absolute;left:155px;width:48px;height:48px;border-radius:50%;background:#2f342c;display:flex;align-items:center;justify-content:center}
.f-lbl{position:absolute;left:225px;color:#fff;font-size:14px;line-height:1.35}
.f-lbl b{font-size:15px}
.f-link{position:absolute;color:#cfd2cc;font-size:14px}
.f-soc{position:absolute;top:3867px;width:38px;height:38px;border-radius:50%;background:#2f342c}
.f-soc::after{content:"";position:absolute;left:13px;top:13px;width:12px;height:12px;border-radius:3px;background:#fff}
</style>
</head>
<body>

<!-- top bar -->
<div class="abs topbar"><span>Welcome to Veltrana Swiss AG</span>
  <i class="soc" style="left:927px"></i><i class="soc" style="left:960px"></i><i class="soc" style="left:994px"></i><i class="soc" style="left:1030px"></i>
</div>

<!-- header -->
<header class="abs header">
  <div class="logo" style="left:155px;top:20px;font-size:20px"><i></i>Veltrana Swiss AG</div>
  <div class="vline" style="left:360px;top:0;height:76px"></div>
  <nav class="nav">
    <a style="left:386px">About</a><a style="left:447px">Our Ingredients</a><a style="left:566px">Partners</a><a style="left:641px">News</a><a style="left:698px">Contact</a>
  </nav>
  <div class="abs" style="left:878px;top:20px;width:36px;height:36px;background:var(--pale-green);display:flex;align-items:center;justify-content:center">
    <svg width="16" height="16" viewBox="0 0 16 16" fill="none" stroke="#333" stroke-width="1.5"><circle cx="7" cy="7" r="5"/><path d="M11 11l4 4"/></svg>
  </div>
  <div class="vline" style="left:936px;top:0;height:76px"></div>
  <div class="abs" style="left:958px;top:20px;width:36px;height:36px;background:#f3f3f3;display:flex;align-items:center;justify-content:center">
    <svg width="18" height="18" viewBox="0 0 18 18" fill="none" stroke="#333" stroke-width="1.4"><circle cx="9" cy="9" r="7.5"/><circle cx="9" cy="7" r="2.5"/><path d="M4.5 14c1.5-2.5 7.5-2.5 9 0"/></svg>
  </div>
  <div class="abs" style="left:1009px;top:20px;width:36px;height:36px;background:#f3f3f3;display:flex;align-items:center;justify-content:center">
    <span role="img" aria-label="Language flag" style="width:18px;height:12px;background:linear-gradient(#c33 0 50%,#fff 50%)"></span>
  </div>
</header>

<!-- hero -->
<div class="abs hero-photo" role="img" aria-label="Natural ingredients on a wooden table: dried orange slices, ginger, honeycomb, oil and herbs"></div>
<svg class="abs" style="left:0;top:420px" width="1200" height="200" viewBox="0 420 1200 200">
  <path d="M0 490 Q560 660 1200 430 L1200 465 Q560 690 0 545 Z" fill="#4f7d0c"/>
  <path d="M0 545 Q560 690 1200 465 L1200 620 L0 620 Z" fill="#fff"/>
</svg>
<div class="abs center hero-text" style="top:226px;font-size:17px">100 % Natural Ingredients</div>
<h1 class="abs center hero-text" style="top:268px;font-size:56px;line-height:62px;font-weight:700">Natural &amp; Functional<br>Ingredients Trader</h1>
<a class="btn" style="left:498px;top:424px;width:200px;height:54px">Discover Now <span class="arr"><svg width="12" height="12" viewBox="0 0 12 12" fill="none" stroke="#fff" stroke-width="1.6"><path d="M2 6h8M7 3l3 3-3 3"/></svg></span></a>
<div class="arrow-btn" style="left:54px;top:333px"><svg width="16" height="16" viewBox="0 0 16 16" fill="none" stroke="#222" stroke-width="1.6"><path d="M13 8H3M7 4L3 8l4 4"/></svg></div>
<div class="arrow-btn" style="left:1106px;top:333px"><svg width="16" height="16" viewBox="0 0 16 16" fill="none" stroke="#222" stroke-width="1.6"><path d="M3 8h10M9 4l4 4-4 4"/></svg></div>

<!-- feature boxes -->
<div class="feat" style="left:155px">
  <svg width="42" height="42" viewBox="0 0 42 42" fill="none" stroke="#222" stroke-width="1.5"><circle cx="21" cy="21" r="18"/><ellipse cx="21" cy="21" rx="8" ry="18"/><path d="M3 21h36M6 12h30M6 30h30"/></svg>
  <b>Worldwide sourcing</b><small>Delivery from just $9.50</small>
</div>
<div class="feat" style="left:459px">
  <svg width="42" height="42" viewBox="0 0 42 42" fill="none" stroke="#222" stroke-width="1.5"><circle cx="21" cy="17" r="12"/><circle cx="21" cy="17" r="7"/><path d="M14 27l-4 12 6-3 3 5 2-10M28 27l4 12-6-3-3 5-2-10"/></svg>
  <b>Best Quality</b><small>ISO 22000 certified</small>
</div>
<div class="feat" style="left:764px">
  <svg width="42" height="42" viewBox="0 0 42 42" fill="none" stroke="#222" stroke-width="1.5"><path d="M7 24v-5a14 14 0 0 1 28 0v5"/><rect x="4" y="22" width="7" height="11" rx="3"/><rect x="31" y="22" width="7" height="11" rx="3"/><path d="M35 33c0 4-5 6-10 6"/></svg>
  <b>Expert Support Team</b><small>Customer 48 hours resolve</small>
</div>

<!-- values -->
<section>
  <div class="abs values-bg"></div>
  <div class="eyebrow center" style="top:884px">Features</div>
  <h2 class="h2 center" style="top:910px">Our Values</h2>
  <div class="abs bottle" role="img" aria-label="Dropper bottle of plant extract with green leaves and softgel capsules"></div>
  <div class="pill" style="left:155px;top:986px;--c:#4aa63a"><i></i>Sourcing of Natural and<br>Health Ingredients</div>
  <div class="pill" style="left:155px;top:1068px;--c:#e03b3b"><i></i>Health &amp; Nutritional Health</div>
  <div class="pill" style="left:155px;top:1150px;--c:#3aa0c9"><i></i>Eco-friendly and Sustainability</div>
  <div class="pill" style="left:155px;top:1232px;--c:#f0a830"><i></i>High Quality Standard in<br>Products and Logistic Services</div>
  <div class="pill" style="left:717px;top:986px;--c:#f0912c"><i></i>Trust and Reliability</div>
  <div class="pill" style="left:717px;top:1068px;--c:#2f7fbf"><i></i>Flexibility &amp; Speed to Market</div>
  <div class="pill" style="left:717px;top:1150px;--c:#ffc000"><i></i>Technical Advice for the<br>Development of New Products</div>
  <div class="pill" style="left:717px;top:1232px;--c:#e8b42a"><i></i>Security of Supply</div>
</section>

<!-- ingredients -->
<section>
  <div class="eyebrow center" style="top:1430px">What We Offer</div>
  <h2 class="h2 center" style="top:1455px">Our Ingredients</h2>
  <div class="ing-img" style="left:155px;background:linear-gradient(160deg,#f4f4f2,#9fb27a 60%,#e9e2c9)" role="img" aria-label="Fresh rosemary sprigs with olive oil"></div>
  <div class="ing-img" style="left:459px;background:radial-gradient(circle at 50% 50%,#b0304a,#e58a2a 45%,#e9ece6 75%)" role="img" aria-label="Fresh fruits and vegetables rich in vitamins"></div>
  <div class="ing-img" style="left:764px;background:radial-gradient(circle at 50% 50%,#c98a3a,#9a3a2a 40%,#ececec 75%)" role="img" aria-label="Dried fruits and nuts in a wooden box"></div>
  <div class="ing-label" style="left:194px">Natural Plant Extracts</div>
  <div class="ing-label" style="left:499px">Natural Vitamins</div>
  <div class="ing-label" style="left:803px">Vegan Ingredients</div>
  <a class="btn" style="left:512px;top:1808px;width:176px;height:54px">View All <span class="arr"><svg width="12" height="12" viewBox="0 0 12 12" fill="none" stroke="#fff" stroke-width="1.6"><path d="M2 6h8M7 3l3 3-3 3"/></svg></span></a>
</section>

<!-- offer -->
<section>
  <div class="abs offer-bg"></div>
  <div class="abs offer-img" role="img" aria-label="Apricots on a wooden board with green leaves and white blossoms"></div>
  <h2 class="h2" style="left:155px;top:1983px;line-height:47px">Get 10% off on Natural<br>Anti-oxidants</h2>
  <div class="eyebrow" style="left:155px;top:2090px">Grab The Offer</div>
  <div class="count" style="left:156px">4</div><div class="count" style="left:223px">12</div><div class="count" style="left:289px">55</div><div class="count" style="left:356px">15</div>
  <div class="count-l" style="left:144px">DAYS</div><div class="count-l" style="left:211px">HOURS</div><div class="count-l" style="left:277px">MINUTES</div><div class="count-l" style="left:344px">SECONDS</div>
  <a class="btn" style="left:155px;top:2218px;width:176px;height:54px">Shop Now <span class="arr"><svg width="12" height="12" viewBox="0 0 12 12" fill="none" stroke="#fff" stroke-width="1.6"><path d="M2 6h8M7 3l3 3-3 3"/></svg></span></a>
</section>

<!-- about -->
<section>
  <div class="abs" style="left:155px;top:2395px;width:399px;height:366px;background:radial-gradient(circle at 55% 40%,#8a1f2a 0,transparent 30%),linear-gradient(135deg,#2f5a22,#5c8a3a 50%,#243f1a)" role="img" aria-label="Hand harvesting ripe coffee cherries from a green plant"></div>
  <div class="eyebrow" style="left:613px;top:2410px">About Us</div>
  <h2 class="h2" style="left:613px;top:2436px;line-height:47px">We Grow Pure,<br>Organic Products</h2>
  <p class="abs" style="left:612px;top:2550px;width:430px;font-size:14px;line-height:22.5px;color:var(--muted);font-weight:300">Veltrana Swiss AG in Ustermatt is a Company limited by shares (AG) from the sector in Trading in food products. The purpose of the company is the production of and trade in food, food additives, raw materials and active ingredients, taking on representations, technical advice and trade.</p>
  <a class="btn" style="left:612px;top:2691px;width:173px;height:54px">Learn More <span class="arr"><svg width="12" height="12" viewBox="0 0 12 12" fill="none" stroke="#fff" stroke-width="1.6"><path d="M2 6h8M7 3l3 3-3 3"/></svg></span></a>
</section>

<!-- news -->
<section>
  <div class="eyebrow center" style="top:2889px">Articles</div>
  <h2 class="h2 center" style="top:2915px">Our Latest News</h2>
  <div class="news-img" style="left:155px;background:radial-gradient(circle at 50% 50%,#f07a1c,#9a6a44 45%,#6a4a33)" role="img" aria-label="Orange cordyceps mushrooms on wood"></div>
  <div class="news-img" style="left:459px;background:linear-gradient(135deg,#b5a68a,#6d8a48 45%,#c7a35a)" role="img" aria-label="Rosemary sprigs beside jars of extract"></div>
  <div class="news-img" style="left:764px;background:radial-gradient(circle at 40% 40%,#a51c2a,#7a2030 40%,#6c7a5a 75%)" role="img" aria-label="Tart topped with fresh cranberries"></div>
  <div class="date" style="left:181px">10<br><span style="font-size:12px">Apr</span></div>
  <div class="date" style="left:486px">10<br><span style="font-size:12px">Apr</span></div>
  <div class="date" style="left:790px">10<br><span style="font-size:12px">Apr</span></div>
  <div class="meta" style="left:155px">By Mira Lenz &nbsp;<span style="color:#ccc">|</span>&nbsp; 3 Comments</div>
  <div class="meta" style="left:459px">By Mira Lenz &nbsp;<span style="color:#ccc">|</span>&nbsp; 3 Comments</div>
  <div class="meta" style="left:764px">By Mira Lenz &nbsp;<span style="color:#ccc">|</span>&nbsp; 3 Comments</div>
  <h3 class="ntitle" style="left:155px">Medicinal Values &amp; Prospect of Cordyceps Extract</h3>
  <h3 class="ntitle" style="left:459px">Rosemary Extract: Natural Antioxidant and Preservative</h3>
  <h3 class="ntitle" style="left:764px">Market Segmentation of Cranberry Extract</h3>
  <i class="dot" style="left:562px"></i><i class="dot" style="left:584px;background:var(--red)"></i><i class="dot" style="left:606px"></i><i class="dot" style="left:628px"></i>
</section>

<!-- newsletter -->
<div class="abs footer-bg"></div>
<svg class="abs" style="left:0;top:3490px" width="1200" height="80" viewBox="0 0 1200 80">
  <path d="M0 50 Q300 0 1200 10 L1200 65 L0 65 Z" fill="var(--green-dark)"/>
  <path d="M0 65 Q400 30 1200 40 L1200 80 L0 80 Z" fill="var(--footer)"/>
</svg>
<div class="abs news-red">
  <div class="abs" style="left:51px;top:38px;font-size:16px">Don't Miss Our Deals</div>
  <div class="abs" style="left:51px;top:64px;font-size:34px;line-height:38px;font-weight:600">Exclusive Offers<br>&amp; Sale</div>
</div>
<div class="abs news-green">
  <div class="abs" style="left:86px;top:38px;font-size:17px">Sign up and get a voucher of worth $250.00</div>
  <div class="abs" style="left:67px;top:89px;width:228px;height:45px;background:#fff;border-radius:23px 0 0 23px;font-size:14px;color:#999;padding:15px 0 0 22px">Email address</div>
  <div class="abs" style="left:295px;top:89px;width:168px;height:45px;background:var(--red);border-radius:0 23px 23px 0;color:#fff;font-weight:700;font-size:18px;text-align:center;padding-top:13px">Subscribe</div>
</div>

<!-- footer -->
<footer>
  <div class="abs" style="left:155px;top:3643px;width:888px;height:1px;background:#3a3f37"></div>
  <div class="vline" style="left:419px;top:3643px;height:302px;background:#3a3f37"></div>
  <div class="vline" style="left:779px;top:3643px;height:302px;background:#3a3f37"></div>

  <div class="f-ico" style="top:3701px"><svg width="20" height="16" viewBox="0 0 20 16" fill="none" stroke="#ddd" stroke-width="1.4"><rect x="1" y="1" width="18" height="14" rx="1"/><path d="M1 2l9 7 9-7"/></svg></div>
  <div class="f-lbl" style="top:3706px"><b>Email</b><br>info@veltranaswiss.com</div>
  <div class="f-ico" style="top:3773px"><svg width="18" height="18" viewBox="0 0 18 18" fill="none" stroke="#ddd" stroke-width="1.4"><path d="M4 1l3 4-2 2c1 2 3 4 5 5l2-2 4 3-2 3C7 16 2 11 1 4z"/></svg></div>
  <div class="f-lbl" style="top:3778px"><b>Phone</b><br>044.5.210.387</div>
  <div class="f-ico" style="top:3844px"><svg width="16" height="20" viewBox="0 0 16 20" fill="none" stroke="#ddd" stroke-width="1.4"><path d="M8 19S1 12 1 7a7 7 0 0 1 14 0c0 5-7 12-7 12z"/><circle cx="8" cy="7" r="2.5"/></svg></div>
  <div class="f-lbl" style="top:3849px"><b>Address</b><br>Talacker 9, 8610<br>Ustermatt, Switzerland</div>

  <div class="logo" style="left:490px;top:3700px;font-size:24px;color:#fff"><i style="background:#fff;width:32px;height:32px"></i>Veltrana Swiss AG</div>
  <p class="abs" style="left:440px;top:3782px;width:318px;text-align:center;color:#cfd2cc;font-size:14px;line-height:21px;font-weight:300">Veltrana Swiss AG in Ustermatt is a Company limited by shares (AG) from the sector in Trading in food products.</p>
  <i class="f-soc" style="left:498px"></i><i class="f-soc" style="left:554px"></i><i class="f-soc" style="left:610px"></i><i class="f-soc" style="left:665px"></i>

  <div class="abs" style="left:820px;top:3707px;color:#fff;font-weight:700;font-size:16px">Important Links</div>
  <a class="f-link" style="left:821px;top:3750px">About</a>
  <a class="f-link" style="left:821px;top:3786px">Our Ingredients</a>
  <a class="f-link" style="left:821px;top:3822px">Partners</a>
  <a class="f-link" style="left:821px;top:3857px">News</a>
  <a class="f-link" style="left:821px;top:3893px">Contact</a>
  <a class="f-link" style="left:965px;top:3750px">Account</a>
  <a class="f-link" style="left:965px;top:3786px">Help</a>
  <a class="f-link" style="left:965px;top:3822px">Support</a>
  <a class="f-link" style="left:965px;top:3857px">FAQ</a>

  <div class="abs" style="left:155px;top:3947px;width:888px;height:1px;background:#3a3f37"></div>
  <div class="abs center" style="top:3965px;color:#cfd2cc;font-size:14px">© Copyright 2022 Veltrana Swiss AG. All Rights Reserved.</div>
</footer>

</body>
</html>
```